Satchel & Sundial needs new business card design

I need a new business card design. I'm looking for out-of-the-box design which represents the freedom of being a location independent entrepreneur.
I offer coaching, retreats and trips.
I would like to see designs with and without the photo.
Colors I use are black (#000000), green (#25A796) and brown (#D7C38C)
Website satchelandsundial.example

Target Market(s)

location independent entrepreneurs, digital nomads, people looking to swap the 9 to 5 for a lifestyle business

Industry/Entity Type

Business

Contact Information for Business Card

Dorota Falkner
Your Lifestyle Business Coach, Retreat & Trip Leader
http://satchelandsundial.example
hello@satchelandsundial.example
Build a life that travels well with you

Font styles to use
Serif
Sans Serif

Requirements
Must have
• One side should contain only the logo. I would also consider having the "Build a life that travels well with you" on that side too (depending on how it looks)
• Please show both sides on the designs.

```html
<!DOCTYPE html>
<html lang="en">
<head>
<meta charset="utf-8">
<title>Satchel &amp; Sundial – Business Card</title>
<link rel="stylesheet" href="https://fonts.googleapis.com/css2?family=Open+Sans:wght@400;600;700&display=swap">
<style>
  :root {
    --ink: #1d1b1c;
    --teal: #25a796;
    --paper: #ffffff;
    --text-grey: #555555;
    --backdrop: #5a5a5a;
    --backdrop-dark: #3a3a3a;
  }
  * { margin: 0; padding: 0; box-sizing: border-box; }
  html, body {
    width: 1200px; height: 950px; overflow: hidden;
    background: radial-gradient(ellipse at 50% 40%, var(--backdrop), var(--backdrop-dark));
    font-family: "Open Sans", Arial, sans-serif;
  }
  .stage {
    width: 1200px; height: 950px;
    display: flex; justify-content: center; align-items: center; gap: 90px;
  }
  .card {
    position: relative;
    width: 400px; height: 700px;
    background: var(--paper);
    overflow: hidden;
    box-shadow: 0 12px 30px rgba(0,0,0,.35);
  }
  /* front */
  .card-front .top-band {
    position: absolute; left: 0; top: 0; width: 100%; height: 250px;
    background: var(--ink);
  }
  .card-front .brush-edge-top {
    position: absolute; left: 0; top: 250px; width: 100%; height: 90px;
  }
  .card-front .brush-edge-bottom {
    position: absolute; left: 0; bottom: 0; width: 100%; height: 130px;
  }
  .wordmark {
    font-weight: 700;
    text-transform: uppercase;
    letter-spacing: 2px;
    line-height: 1.1;
    text-align: center;
  }
  .card-front .wordmark {
    position: absolute; left: 0; right: 0; top: 80px;
    color: var(--paper); font-size: 34px;
  }
  .details {
    position: absolute; left: 0; right: 0; top: 365px;
    text-align: center; color: var(--text-grey);
    font-size: 17px; line-height: 1.45;
  }
  .details .name {
    color: var(--teal); font-weight: 700; font-size: 23px;
    letter-spacing: 1.5px; text-transform: uppercase; margin-bottom: 4px;
  }
  .details .role { font-weight: 600; }
  .details .contact { margin-top: 14px; }
  /* back */
  .card-back .wordmark {
    position: absolute; left: 0; right: 0; top: 270px;
    color: var(--ink); font-size: 36px;
  }
  .tagline {
    position: absolute; left: 0; right: 0; top: 400px;
    text-align: center; color: var(--ink);
    font-size: 13px; letter-spacing: 1.5px; text-transform: uppercase;
  }
  .social {
    position: absolute; right: 22px; bottom: 22px;
    display: flex; gap: 6px;
  }
  .social span {
    width: 18px; height: 18px; background: var(--teal); display: block;
  }
</style>
</head>
<body>
<main class="stage">
  <section class="card card-front">
    <div class="top-band"></div>
    <svg class="brush-edge-top" role="img" aria-label="Brushed pine-forest silhouette fading from black into white" viewBox="0 0 400 90" preserveAspectRatio="none">
      <defs>
        <linearGradient id="fadeTop" x1="0" y1="0" x2="0" y2="1">
          <stop offset="0" stop-color="#1d1b1c"/>
          <stop offset="1" stop-color="#1d1b1c" stop-opacity="0"/>
        </linearGradient>
      </defs>
      <rect width="400" height="90" fill="url(#fadeTop)"/>
    </svg>
    <h1 class="wordmark">Satchel &amp;<br>Sundial</h1>
    <div class="details">
      <p class="name">Dorota Falkner</p>
      <p class="role">Your Lifestyle Business Coach<br>Retreat &amp; Trip Leader</p>
      <p class="contact">hello@satchelandsundial.example<br>www.satchelandsundial.example</p>
    </div>
    <svg class="brush-edge-bottom" role="img" aria-label="Brushed teal pine-forest silhouette along the bottom edge" viewBox="0 0 400 130" preserveAspectRatio="none">
      <defs>
        <linearGradient id="fadeBottom" x1="0" y1="0" x2="0" y2="1">
          <stop offset="0" stop-color="#25a796" stop-opacity="0"/>
          <stop offset=".55" stop-color="#25a796" stop-opacity=".85"/>
          <stop offset="1" stop-color="#25a796"/>
        </linearGradient>
      </defs>
      <rect width="400" height="130" fill="url(#fadeBottom)"/>
    </svg>
  </section>

  <section class="card card-back">
    <h2 class="wordmark">Satchel &amp;<br>Sundial</h2>
    <p class="tagline">Build a life that travels well with you</p>
    <div class="social" aria-label="Social links">
      <span></span><span></span><span></span>
    </div>
  </section>
</main>
</body>
</html>
```